Local massage therapist needs some new marketing material

Hi there! I am a massage therapist here in Denver, CO in Alder Bend(shopping and art district) of the city. My business is called Lumo Bodywork of Denver. My practice has an eastern influence and I do reflexology, thai massage and use Chinese herbs, etc. I know all my clients and pay close attention to details. I am also very respectful of tradition and it shows in how I work. I tend to like modern, clean, fun, Asian designs. I am wanting a new business card and brochure. I have a logo and branding for my business that I want used in the design. Currently, the sign for my building is purple and I think my logo was designed to be purple. I will attach pictures of it and can send whatever files are necessary so it can be integrated into the brochure, etc. I like the purple but open to using other colors as well. Thanks!
My website is lumobodyworkofdenver.example where info can be gathered about me and services/fees for brochure.
Updates

Just increased budget. Please see new feedback in discussion thread.

Thanks!

                                       HEY ALL,

Just wanted to let you know that I made a change to my website. It is on the Prices Page. I no longer have the frequent  flyer prices but I added discounts. Let me know if you have any questions. Thanks so much!

Target Market(s)

healthy, urban, educated, upper middle class, yogis

Industry/Entity Type

Marketing

Requirements
Must have
• logo stays purple
Should not have
• not too busy

```html
<!DOCTYPE html>
<html lang="en">
<head>
<meta charset="utf-8">
<title>Lumo Bodywork of Denver – Business Card</title>
<link href="https://fonts.googleapis.com/css2?family=Open+Sans:ital,wght@0,400;0,600;0,700;1,400&display=swap" rel="stylesheet">
<style>
  :root {
    --purple: #5e3196;
    --ink: #4a4a4a;
    --muted: #6d6d6d;
    --rule: #9a9a9a;
    --card: #ffffff;
    --backdrop: #e6e6ea;
  }
  * { box-sizing: border-box; margin: 0; padding: 0; }
  html, body {
    width: 1200px; height: 987px; overflow: hidden;
    background: var(--backdrop);
    font-family: "Open Sans", Arial, sans-serif;
    color: var(--ink);
  }
  .stage { position: relative; width: 1200px; height: 987px; }
  .card {
    position: absolute;
    width: 540px; height: 309px;
    background: var(--card);
    border-radius: 26px;
    box-shadow: 0 6px 18px rgba(0,0,0,0.12);
    overflow: hidden;
  }
  .card--front { left: 40px; top: 339px; }
  .card--back  { left: 620px; top: 339px; }

  /* Brand lockup */
  .brand {
    position: absolute;
    display: flex; flex-direction: column; align-items: center;
    color: var(--purple);
  }
  .brand__dot {
    border-radius: 50%;
    background: var(--purple);
  }
  .brand__name { font-weight: 600; line-height: 1; }
  .card--front .brand { right: 36px; bottom: 34px; }
  .card--front .brand__dot { width: 46px; height: 46px; margin-bottom: 10px; }
  .card--front .brand__name { font-size: 50px; letter-spacing: 4px; }
  .card--back .brand { right: 30px; top: 72px; }
  .card--back .brand__dot { width: 36px; height: 36px; margin-bottom: 8px; }
  .card--back .brand__name { font-size: 38px; letter-spacing: 3px; }

  /* Front */
  .accent-bar {
    position: absolute; left: 34px; top: 22px;
    width: 9px; height: 40px; background: var(--purple);
  }
  .holder { position: absolute; left: 56px; top: 22px; }
  .holder__name { color: var(--purple); font-weight: 700; font-size: 21px; line-height: 1.1; }
  .holder__title { font-size: 14px; color: var(--muted); }
  .address {
    position: absolute; left: 40px; top: 106px;
    font-size: 15px; line-height: 1.3;
  }
  .contact {
    position: absolute; left: 40px; top: 176px;
    list-style: none; font-size: 13px; line-height: 1.55;
  }
  .contact li { display: flex; align-items: center; gap: 6px; }
  .contact svg { width: 12px; height: 12px; fill: var(--purple); flex: none; }
  .website { position: absolute; left: 40px; top: 240px; font-size: 13px; }

  /* Back */
  .appt { position: absolute; left: 30px; top: 26px; width: 320px; }
  .appt__heading {
    color: var(--purple); font-weight: 700; font-size: 14px;
    letter-spacing: 0.3px; margin-bottom: 14px;
  }
  .field { display: flex; align-items: flex-end; font-size: 14px; margin-bottom: 10px; }
  .field__line { flex: 1; border-bottom: 1px dotted var(--rule); margin: 0 6px 4px; }
  .hours { font-size: 14px; line-height: 1.4; margin-top: 8px; }
  .notice { font-size: 13px; font-style: italic; color: var(--muted); margin-top: 8px; }
</style>
</head>
<body>
<main class="stage">

  <section class="card card--front" aria-label="Business card front">
    <span class="accent-bar"></span>
    <div class="holder">
      <p class="holder__name">Your Name</p>
      <p class="holder__title">Title</p>
    </div>
    <p class="address">1418 E Alder St, Denver<br>CO 80299</p>
    <ul class="contact">
      <li>
        <svg viewBox="0 0 24 24" aria-hidden="true"><path d="M6.6 10.8a15.1 15.1 0 0 0 6.6 6.6l2.2-2.2c.3-.3.7-.4 1-.2 1.1.4 2.3.6 3.6.6.6 0 1 .4 1 1V20c0 .6-.4 1-1 1C10.6 21 3 13.4 3 4c0-.6.4-1 1-1h3.5c.6 0 1 .4 1 1 0 1.3.2 2.5.6 3.6.1.3 0 .7-.2 1z"/></svg>
        303.555.0148
      </li>
      <li>
        <svg viewBox="0 0 24 24" aria-hidden="true"><path d="M2 5h20v14H2zm2 2v.5l8 5 8-5V7l-8 5z"/></svg>
        info@lumobodyworkofdenver.example
      </li>
    </ul>
    <p class="website">www.lumobodyworkofdenver.example</p>
    <div class="brand">
      <span class="brand__dot"></span>
      <span class="brand__name">LUMO</span>
    </div>
  </section>

  <section class="card card--back" aria-label="Business card back">
    <div class="appt">
      <p class="appt__heading">YOUR APPOINTMENT</p>
      <div class="field">Name :<span class="field__line"></span></div>
      <div class="field">Date :<span class="field__line"></span>Time :<span class="field__line"></span>am / pm</div>
      <p class="hours">Tues - Fri 10am - 8pm Sat 10am-5pm<br>(Appointments required) No walk-ins please.</p>
      <p class="notice">We appreciate a 24 hr. notice for cancellations</p>
    </div>
    <div class="brand">
      <span class="brand__dot"></span>
      <span class="brand__name">LUMO</span>
    </div>
  </section>

</main>
</body>
</html>
```